Design the Business card for NetVaultic

Business card required for a professional Cyber Security business.
Company Logo and Icon has already been provided however I would like other options for the logo and icon to compare to. Alternatively, please refine/enhance the image of the logo.icon I have already provided.

If you are going to use the provided logo and icon, I was thinking that the company raised Logo on White background would serve well on the front of the card. See attached. AND, a large company raised stand-alone icon to appear on black background on the back of the card with tagline 'Cyber Risk Management, Governance and Consulting' or 'Cyber Security for your Business' See attached.
Alternatively, provide your own design for the logo and icon.

Target Market(s)

Enterprise, Government, Financial.

Contact Information for Business Card

Tavin Orloweth
Founder and CEO

Email Address
Mobile Number
Website URL
LinkedIn URL

Logo Text

NetVaultic - see attached example of logo

Font styles to use
Other font styles liked:
• Berlin Sans FB

Requirements
Must have
• Clean large and bold icon on the back with tagline.
• Horizontal alignment,
Nice to have
• Round edges.
• Raised Logo/Icon
Should not have
• An unprofessional look and feel.

```html
<!DOCTYPE html>
<html lang="en">
<head>
<meta charset="utf-8">
<title>NetVaultic Business Card</title>
<link rel="stylesheet" href="https://fonts.googleapis.com/css2?family=Fredoka:wght@500&family=Roboto:wght@400&display=swap">
<style>
  :root {
    --backdrop: #2b2b2b;
    --brand-blue: #0a6bb5;
    --accent-blue: #4a6fc4;
    --accent-yellow: #f2b705;
    --card-white: #f3f3f3;
    --card-black: #1c1d1f;
    --text-white: #ffffff;
  }
  * { margin: 0; padding: 0; box-sizing: border-box; }
  html, body { width: 1200px; height: 960px; overflow: hidden; }
  body { background: var(--backdrop); position: relative; font-family: "Roboto", sans-serif; }

  .card { position: absolute; width: 600px; height: 342px; overflow: hidden; box-shadow: 0 4px 10px rgba(0,0,0,0.5); }

  .card-front { left: 314px; top: 113px; background: var(--brand-blue); }
  .front-panel {
    position: absolute; left: 259px; top: 0; width: 341px; height: 342px;
    background: var(--card-white);
    border-radius: 70px 0 0 150px;
    display: flex; align-items: center; justify-content: center; gap: 12px;
  }
  .panel-dot { width: 34px; height: 34px; border-radius: 50%; background: var(--accent-yellow); }
  .panel-name { font-family: "Fredoka", sans-serif; font-weight: 500; font-size: 40px; color: var(--brand-blue); }

  .holder-name { position: absolute; left: 46px; top: 48px; font-family: "Fredoka", sans-serif; font-weight: 500; font-size: 20px; color: var(--accent-yellow); }
  .holder-title { position: absolute; left: 45px; top: 72px; font-family: "Fredoka", sans-serif; font-weight: 500; font-size: 14px; color: var(--text-white); }

  .contact-list { position: absolute; left: 46px; top: 218px; list-style: none; }
  .contact-item { display: flex; align-items: center; gap: 9px; height: 19px; font-size: 14px; color: var(--text-white); }
  .contact-icon { width: 14px; height: 14px; flex: none; }

  .card-back { left: 311px; top: 473px; background: var(--card-black); }
  .back-brand { position: absolute; left: 125px; top: 140px; display: flex; align-items: center; gap: 14px; }
  .brand-dot { width: 78px; height: 78px; border-radius: 50%; background: var(--accent-blue); }
  .brand-name { font-family: "Fredoka", sans-serif; font-weight: 500; font-size: 46px; color: var(--brand-blue); }
  .tagline { position: absolute; left: 0; right: 0; top: 276px; text-align: center; font-family: "Fredoka", sans-serif; font-weight: 500; font-size: 17px; }
  .tagline-blue { color: var(--accent-blue); }
  .tagline-yellow { color: var(--accent-yellow); }
</style>
</head>
<body>
  <section class="card card-front">
    <div class="holder-name">Tavin Orloweth</div>
    <div class="holder-title">Founder &amp; CEO</div>
    <ul class="contact-list">
      <li class="contact-item">
        <svg class="contact-icon" viewBox="0 0 14 14"><rect x="3.5" y="0.5" width="7" height="13" rx="1.5" fill="none" stroke="#f2b705" stroke-width="1.6"/><circle cx="7" cy="11" r="0.9" fill="#f2b705"/></svg>
        555 014 2738
      </li>
      <li class="contact-item">
        <svg class="contact-icon" viewBox="0 0 14 14"><rect x="0.5" y="3" width="13" height="9" fill="#f2b705"/><path d="M0.5 3 L7 8 L13.5 3" fill="none" stroke="#0a6bb5" stroke-width="1.2"/></svg>
        tavin@netvaultic.com
      </li>
      <li class="contact-item">
        <svg class="contact-icon" viewBox="0 0 14 14"><circle cx="7" cy="7" r="6.3" fill="#f2b705"/><path d="M1 7 H13 M7 1 C4 4 4 10 7 13 M7 1 C10 4 10 10 7 13" fill="none" stroke="#0a6bb5" stroke-width="1"/></svg>
        www.netvaultic.com
      </li>
      <li class="contact-item">
        <svg class="contact-icon" viewBox="0 0 14 14"><circle cx="7" cy="7" r="6.3" fill="#f2b705"/></svg>
        netvaultic
      </li>
    </ul>
    <div class="front-panel">
      <span class="panel-dot"></span>
      <span class="panel-name">NetVaultic</span>
    </div>
  </section>

  <section class="card card-back">
    <div class="back-brand">
      <span class="brand-dot"></span>
      <span class="brand-name">NetVaultic</span>
    </div>
    <p class="tagline"><span class="tagline-blue">Cyber Risk Management, </span><span class="tagline-yellow">Governance &amp; Consulting</span></p>
  </section>
</body>
</html>
```